Plume Dishwasher Pods (Pack design) *

We require a doy pack design for a new dishwasher pod brand. It aims at competing with the top tier global brands, and hence needs to have 'big brand feel'. The product is of high quality, slightly lower priced and hence makes "Plume" for the consumer to purchase.

The design should be clean, sophisticated, modern, and appeal to the upper end consumer.

What's important, is that the consumer is habitually buying the known-brand, and hence we need to quickly and visually establish what the product is (dishwashing tablet) and also establish trust (the product will deliver). Hence we can borrow equity from category cues (see design brief)

Target Market(s)

Upper LSM (mid to higher end of the market). Dishwasher penetration is low, and hence only the top end of the market has a dishwasher

Industry/Entity Type

Cleaning Product

Font styles to use
Sans Serif

Colors
ffffff
000000
0255a3
33a6d7
fbee3d
add136

Requirements
Must have
• Message/Idea/Visual Hierarchy:
• Priority 1: Category / Product Type (i.e. "Dishwasher Pods"). Category most important, then the brand name. Could be joined. This must be clear, and stand out!
• Priority 2: Efficient cleaning pod/tablet which cleans thoroughly (scienctific cues, sparkles, foam, lemon/lime, etc.). Please use 3D art, rather than flat artwork. The idea that we may be well priced, but the technology is state-of-the-art. People are taking a risk buying us, so we need to comfort them that the product will work! We need to establish brand trust with our serious and professional look.
• Priority 3: Stand-out, bold, clean, modern, simple design. Simple doesn't mean "no class and style". Competitors have busy packaging with lots of colours and text.
• Lastly: We are "sensible" (in terms of cost and efficiency), "conscious", "have values". We may partner with a "Save Water" organisation. Hence the feeling of "values" and the "human touch" is a nice-to-have. We may be serious in packaging, but we care about you, your pocket, society and the environment. Hence you can contact us on chirpa for instant-chat (see packagaing text).
Nice to have
• - A simple placeholder 'back of pack' text "Lorem ipsum". No need for excessive design, this will be worked upon in Round 2 with the winning design(er).
• - In a world where clean modern and computers dominate, there can be perfection in imperfection. There can be a personal (human) touch added. Think detailed droplets, or 3D/natural feel.
• - Dummy barcode
• - As for the colours, we are very open to ideas and the given colours in the project was only a guideline. Don't necessarily stick to them - we encourage creativity.
Should not have
• The brand is not:
• - Cheap and cheesy and cartoonish (as most competitors). Instead we are 3D, real!
• - Busy and tiring on the eye (as the lead competitor). It can be bold, stylish, eye-catching, but not overly busy and dainty. Think of Fennix (infancy days) vs Wumbo (market leader days).

```html
<!DOCTYPE html>
<html lang="en">
<head>
<meta charset="utf-8">
<title>Plume Dishwasher Pods – Pack Front</title>
<link rel="stylesheet" href="https://fonts.googleapis.com/css2?family=Saira+Semi+Expanded:wght@700;800&family=Lexend:wght@500&display=swap">
<style>
  :root {
    --canvas-bg: #eef0f2;
    --pack-edge: #a3cfee;
    --pack-mid: #d4eaf8;
    --pack-core: #ffffff;
    --brand-blue: #1f8fd0;
    --deep-blue: #1e3f9e;
    --pill-blue: #2440a8;
    --badge-blue: #1a3a9a;
    --white: #ffffff;
    --zip-line: rgba(110, 165, 210, 0.5);
    --network-tone: #b6dbf3;
    --network-deep: #9cc9ea;
  }
  * { box-sizing: border-box; margin: 0; padding: 0; }
  html, body {
    width: 1200px;
    height: 1200px;
    overflow: hidden;
    background: var(--canvas-bg);
  }
  .canvas {
    position: relative;
    width: 1200px;
    height: 1200px;
  }
  .pack-front {
    position: absolute;
    left: 280px;
    top: 30px;
    width: 640px;
    height: 1140px;
    border-radius: 18px;
    overflow: hidden;
    background:
      radial-gradient(ellipse 60% 42% at 55% 44%, var(--pack-core) 0%, var(--pack-core) 50%, var(--pack-mid) 80%, var(--pack-edge) 100%);
  }
  .zip-band {
    position: absolute;
    left: 0;
    right: 0;
    top: 72px;
    height: 66px;
    border-top: 2px solid var(--zip-line);
    border-bottom: 2px solid var(--zip-line);
    background: linear-gradient(180deg, rgba(163,207,238,0.6), rgba(212,234,248,0.3));
  }
  .network-side {
    position: absolute;
    left: 0;
    top: 140px;
    width: 130px;
    height: 820px;
    background:
      radial-gradient(ellipse 80% 30% at 20% 30%, rgba(156,201,234,0.65), rgba(156,201,234,0) 100%),
      radial-gradient(ellipse 80% 25% at 30% 75%, rgba(156,201,234,0.55), rgba(156,201,234,0) 100%),
      linear-gradient(90deg, rgba(163,207,238,0.8), rgba(212,234,248,0));
  }
  .network-lower {
    position: absolute;
    left: 0;
    right: 0;
    bottom: 0;
    height: 380px;
    background:
      radial-gradient(ellipse 40% 35% at 25% 70%, rgba(156,201,234,0.7), rgba(156,201,234,0) 100%),
      radial-gradient(ellipse 40% 35% at 75% 55%, rgba(182,219,243,0.8), rgba(182,219,243,0) 100%),
      linear-gradient(180deg, rgba(212,234,248,0) 0%, var(--network-tone) 55%, var(--network-deep) 100%);
  }
  .brand-block {
    position: absolute;
    left: 0;
    right: 0;
    top: 215px;
    display: flex;
    flex-direction: column;
    align-items: center;
  }
  .brand-dot {
    width: 64px;
    height: 64px;
    border-radius: 50%;
    background: var(--brand-blue);
    margin-bottom: 28px;
  }
  .brand-name {
    font-family: "Saira Semi Expanded", sans-serif;
    font-weight: 800;
    font-size: 92px;
    line-height: 1;
    letter-spacing: 1px;
    color: var(--brand-blue);
    text-transform: uppercase;
  }
  .category-pill {
    margin-top: 14px;
    padding: 8px 26px;
    border-radius: 24px;
    background: var(--pill-blue);
    color: var(--white);
    font-family: "Lexend", sans-serif;
    font-weight: 500;
    font-size: 25px;
    line-height: 1.2;
    letter-spacing: 1.5px;
    text-transform: uppercase;
  }
  .claim {
    position: absolute;
    left: 0;
    right: 0;
    top: 640px;
    text-align: center;
    font-family: "Saira Semi Expanded", sans-serif;
    font-weight: 700;
    font-size: 56px;
    line-height: 1.18;
    color: var(--deep-blue);
    text-transform: uppercase;
  }
  .count-badge {
    position: absolute;
    left: 58px;
    top: 1002px;
    width: 62px;
    height: 100px;
    border-radius: 6px 6px 0 0;
    background: var(--badge-blue);
    color: var(--white);
    display: flex;
    flex-direction: column;
    align-items: center;
    justify-content: center;
    font-family: "Saira Semi Expanded", sans-serif;
  }
  .count-number {
    font-weight: 800;
    font-size: 36px;
    line-height: 1;
  }
  .count-unit {
    margin-top: 4px;
    padding: 1px 3px;
    border: 1.5px solid var(--white);
    font-weight: 700;
    font-size: 9px;
    letter-spacing: 0.3px;
    text-transform: uppercase;
  }
</style>
</head>
<body>
  <main class="canvas">
    <section class="pack-front" aria-label="Plume Dishwasher Pods pack front">
      <div class="zip-band"></div>
      <div class="network-side" role="img" aria-label="Scientific network of connected dots and lines along the left edge"></div>
      <div class="network-lower" role="img" aria-label="Scientific network of glowing dots joined by fine lines across the lower pack"></div>

      <header class="brand-block">
        <span class="brand-dot" aria-hidden="true"></span>
        <h1 class="brand-name">Plume</h1>
        <p class="category-pill">Dishwasher Pods</p>
      </header>

      <p class="claim">Superior<br>Cleaning</p>

      <div class="count-badge">
        <span class="count-number">54</span>
        <span class="count-unit">Tablets</span>
      </div>
    </section>
  </main>
</body>
</html>
```